July 2022 Industrial Manufacturer Product Expo Mexico City

We manufacture large screws and fastners for large Mining equipment, Trains, large ships, airplanes, wind turbines, and so on. We also do custom work base on the customer needs. No matter the size we can make it.
We have a Expo coming up with companies all over the world. We have to stand out we are a family own business so our customer service will be above and beyond anyone can provide. We do not have a sales force to push our products and services we provide one on one service.
Plus@!! I'm looking for anything that you designers can come up with if it was your company to put on a business card, plus i want to do a 1 or 2 sided pamphlet, and then a website. We make Speciality Bolts for large mining equipment these bolts can be 3 to 4 foot long!!! Plus fasteners, Nuts, washers, any, size, strengths, special materials, we offer more of a ono on one customer service, We are a small company, family own, but can fulfill any type of orders. We can also provide special time lines for emergency orders. "We keep the machines running we here at KRV don't believe in down time" We want to hear any slogan based on our company to stand out.
Thanks i really appreciate all your work and options that we have to pick on. Plus just a thought we could possibly want to entertain a experience Marketing internet help maybe a employment possibility. Thanks

I need 2 cards one in Spanish and English Like the steel back ground maybe send me in some bright red and blue writing Same with the Black cards Please remove the word Military The logo KRV maybe integrate a picture of a Bolt 🔩 Thank you

Still looking for I need 2 cards one in Spanish and English Like the steel back ground maybe send me in some bright red and blue writing Same with the Black cards try bright writing Please remove the word Military The logo KRV maybe integrate a picture of a Bolt 🔩 Plus will need the company to make a brochure and website next Thank you

Target Market(s)

Large Mining, Ship, Train, Green Energy, VELM, and Government equipment. Throughout the World

Industry/Entity Type

We can Custom Manufacture any type of Fastners for Mining equipment, Trains, Ships, Green energy, Governments, or military projects. wind turbines,

Contact Information for Business Card

I attached the name and contact info that's on a card, plus the Company Logo. Would like industrial looking background with Bright Colors that will stand out!! If we can insert somewhere maybe on back that we "Custom Manufacture Any Size or Quantity Fastners for Large Mining Equipment, Trains, Ships, Green Energy Equipment or Government Projects

Font styles to use
Other font styles liked:
• You Pick, has to be bold, colorful standout, Professional looking Beable to read it.

Colors

Designer to choose colors to be used in the design.

Requirements
Must have
• Need in Spanish and English TO STANDOUT FROM THE REST OF THE EXPO!! See Business card details, Rounded corners
Nice to have
• Can i see some of the darker cards with Bright Red and Blue letters I like to see the different type of card material, heavy thickness, plastic, transparent, Metal types, Bright Colors, I saw like Raised letters like on the logo.

```html
<!DOCTYPE html>
<html lang="es">
<head>
<meta charset="utf-8">
<title>KRV — Tarjetas de presentación</title>
<link rel="stylesheet" href="https://fonts.googleapis.com/css2?family=Roboto+Condensed:wght@400;700&family=Roboto:wght@400&display=swap">
<style>
  :root {
    --bg: #262626;
    --card-black: #1b1b1d;
    --card-black-edge: #2a2a2d;
    --card-white: #fbfbfb;
    --ink-dark: #3a3a3e;
    --ink-grey: #555a60;
    --navy: #1a2a8c;
    --blue: #0b6fc1;
    --cyan: #19a6dc;
    --silver: #8a8c90;
    --emboss: #0f0f10;
  }
  * { margin: 0; padding: 0; box-sizing: border-box; }
  html, body { width: 1200px; height: 874px; overflow: hidden; }
  body {
    background: var(--bg);
    font-family: "Roboto Condensed", "Arial Narrow", sans-serif;
    position: relative;
  }
  .card {
    position: absolute;
    left: 340px;
    width: 520px;
    height: 297px;
    border-radius: 20px;
    overflow: hidden;
  }
  /* ---------- front ---------- */
  .card--front {
    top: 110px;
    background: linear-gradient(160deg, var(--card-black-edge) 0%, var(--card-black) 55%, #141415 100%);
  }
  .front-mark {
    position: absolute;
    top: 88px;
    left: 0;
    width: 100%;
    text-align: center;
  }
  .front-mark__name {
    font-weight: 700;
    font-size: 78px;
    letter-spacing: 10px;
    line-height: 1;
    color: var(--silver);
  }
  .front-mark__tagline {
    margin-top: 10px;
    font-size: 15px;
    letter-spacing: 1.5px;
    color: var(--silver);
  }
  /* ---------- back ---------- */
  .card--back {
    top: 467px;
    background: var(--card-white);
  }
  .back-mark {
    position: absolute;
    top: 34px;
    right: 36px;
    text-align: right;
  }
  .back-mark__name {
    font-weight: 700;
    font-size: 52px;
    letter-spacing: 7px;
    line-height: 1;
    color: var(--ink-dark);
  }
  .back-mark__tagline {
    margin-top: 6px;
    font-size: 11px;
    letter-spacing: 0.8px;
    color: var(--navy);
  }
  .holder {
    position: absolute;
    top: 138px;
    left: 40px;
    width: 440px;
  }
  .holder__name {
    font-weight: 700;
    font-size: 20px;
    color: var(--navy);
  }
  .holder__name .given { color: var(--blue); }
  .holder__role {
    font-size: 13px;
    color: var(--ink-grey);
    margin-top: 1px;
  }
  .holder__rule {
    margin-top: 8px;
    height: 1px;
    background: linear-gradient(90deg, var(--navy), var(--cyan) 40%, var(--navy));
  }
  .contact {
    margin-top: 9px;
    font-family: "Roboto", Arial, sans-serif;
    font-size: 12px;
    color: var(--ink-grey);
    list-style: none;
  }
  .contact li {
    display: flex;
    align-items: center;
    gap: 6px;
    margin-bottom: 4px;
  }
  .contact svg { width: 11px; height: 11px; flex: none; }
  .contact .sep { margin-left: 8px; }
  .edge-band {
    position: absolute;
    left: 0;
    bottom: 0;
    width: 100%;
    height: 14px;
    display: flex;
  }
  .edge-band__blue {
    width: 64%;
    background: linear-gradient(90deg, var(--navy), var(--cyan) 60%, var(--blue));
  }
  .edge-band__gap { width: 3px; background: var(--card-white); }
  .edge-band__steel {
    flex: 1;
    background: linear-gradient(90deg, #111, #4a4a4e 60%, #1c1c1e);
  }
</style>
</head>
<body>

  <section class="card card--front" aria-label="Frente de la tarjeta">
    <div class="front-mark">
      <div class="front-mark__name">KRV</div>
      <div class="front-mark__tagline">FABRICACION Y DISTRIBUCION DE TORNILLOS</div>
    </div>
  </section>

  <section class="card card--back" aria-label="Reverso de la tarjeta">
    <div class="back-mark">
      <div class="back-mark__name">KRV</div>
      <div class="back-mark__tagline">FABRICACION Y DISTRIBUCION DE TORNILLOS</div>
    </div>

    <div class="holder">
      <div class="holder__name">Lic. <span class="given">Mariela Fuentes</span> Ortiz</div>
      <div class="holder__role">Cotizaciones en</div>
      <div class="holder__rule"></div>
      <ul class="contact">
        <li>
          <svg viewBox="0 0 12 12" aria-hidden="true"><path fill="#1a2a8c" d="M2.4 0.6l2 2-1 1.3c.7 1.5 1.9 2.7 3.4 3.4l1.3-1 2 2-1.2 1.6C5 9.6 2.4 7 .8 1.8z"/></svg>
          <span>5550142233</span>
          <svg class="sep" viewBox="0 0 12 12" aria-hidden="true"><rect x="3" y="0.5" width="6" height="11" rx="1" fill="none" stroke="#0b6fc1" stroke-width="1.3"/></svg>
          <span>5550198841</span>
        </li>
        <li>
          <svg viewBox="0 0 12 12" aria-hidden="true"><rect x="0.5" y="2" width="11" height="8" fill="#0b6fc1"/><path d="M0.5 2l5.5 4.5L11.5 2" fill="none" stroke="#fff" stroke-width="1"/></svg>
          <span>krvtornilleria.ventas@mail.com</span>
        </li>
      </ul>
    </div>

    <div class="edge-band">
      <div class="edge-band__blue"></div>
      <div class="edge-band__gap"></div>
      <div class="edge-band__steel"></div>
    </div>
  </section>

</body>
</html>
```